KBT Business Cards

We require business cards for our business. We would like a matte black back to the card, with our logo centred in the middle. The front side of the card is open to design.

Target Market(s)

Clients looking for legal services (professional)

Industry/Entity Type

Legal

Contact Information for Business Card

Doran Kelbrath
Partner
Mobile: 0461 738 524
Email: doran@kbtlaw.co
Website: www.kbtlaw.co
Level 3, 118 Wendmore Street
Sydney NSW 2000

Font styles to use
Other font styles liked:
• Avenir

Colors
f04a50
ffffff
1b1b1b

Requirements
Must have
• Black back with logo included in the centre of the card.
• Our font is Avenir.

```html
<!DOCTYPE html>
<html lang="en">
<head>
<meta charset="utf-8">
<title>Kelbrath Bristow Legal – Business Cards</title>
<link href="https://fonts.googleapis.com/css2?family=Nunito+Sans:wght@400;600;700;800&display=swap" rel="stylesheet">
<style>
  :root{
    --stage:#0c2333;
    --card-black:#1b1b1b;
    --card-white:#f5f6f8;
    --brand-red:#b82040;
    --ink:#1b1b1b;
    --ink-soft:#3a3a3a;
    --white:#ffffff;
  }
  *{margin:0;padding:0;box-sizing:border-box}
  html,body{width:1200px;height:907px;overflow:hidden}
  body{
    background:var(--stage);
    font-family:"Nunito Sans",Arial,sans-serif;
    position:relative;
  }
  .card{
    position:absolute;
    top:288px;
    width:540px;height:330px;
    box-shadow:0 14px 30px rgba(0,0,0,.45);
    overflow:hidden;
  }
  .card--back{left:40px;background:var(--card-black)}
  .card--front{left:620px;background:var(--card-white)}

  /* brand lockup */
  .lockup{display:flex;align-items:center;gap:14px}
  .lockup__mark{display:block;flex:none}
  .lockup__name{
    font-weight:700;text-transform:uppercase;letter-spacing:.02em;
    line-height:1.02;
  }
  .card--back .lockup{
    position:absolute;left:50%;top:50%;transform:translate(-50%,-50%);
  }
  .card--back .lockup__mark{width:54px;height:54px;background:var(--brand-red)}
  .card--back .lockup__name{color:var(--white);font-size:30px}

  /* front */
  .front__band{position:absolute;left:0;top:0;bottom:0;width:58px;background:var(--brand-red)}
  .front__rule{position:absolute;left:58px;top:0;bottom:0;width:6px;background:var(--ink)}
  .card--front .lockup{position:absolute;left:40px;top:40px;gap:12px}
  .card--front .lockup__mark{width:44px;height:44px;background:var(--brand-red);border:3px solid var(--white)}
  .card--front .lockup__name{color:var(--ink);font-size:17px}

  .person{position:absolute;left:96px;top:150px}
  .person__name{color:var(--brand-red);font-weight:800;font-size:27px;line-height:1.1}
  .person__role{color:var(--ink);font-size:16px;font-weight:600;margin-top:4px}

  .contact{position:absolute;left:96px;top:232px;list-style:none}
  .contact__item{display:flex;align-items:center;gap:10px;font-size:14px;color:var(--ink-soft);line-height:24px}
  .contact__icon{width:14px;height:14px;flex:none}
  .contact__accent{color:var(--brand-red)}

  .address{
    position:absolute;right:26px;top:44px;
    padding-left:12px;border-left:2px solid var(--brand-red);
    font-size:13px;line-height:1.45;color:var(--ink-soft);
  }
</style>
</head>
<body>

<section class="card card--back" aria-label="Card back">
  <div class="lockup">
    <span class="lockup__mark"></span>
    <span class="lockup__name">Kelbrath<br>Bristow<br>Legal</span>
  </div>
</section>

<section class="card card--front" aria-label="Card front">
  <div class="front__band"></div>
  <div class="front__rule"></div>

  <div class="lockup">
    <span class="lockup__mark"></span>
    <span class="lockup__name">Kelbrath<br>Bristow<br>Legal</span>
  </div>

  <div class="address">Level 3, 118 Wendmore<br>Street Sydney NSW 2000</div>

  <div class="person">
    <div class="person__name">Doran Kelbrath</div>
    <div class="person__role">Partner</div>
  </div>

  <ul class="contact">
    <li class="contact__item">
      <svg class="contact__icon" viewBox="0 0 14 14" aria-hidden="true"><circle cx="7" cy="7" r="7" fill="#b82040"/><path d="M4.2 3.6l1.5-.4.8 1.8-.9.7a4.5 4.5 0 0 0 2.1 2.1l.7-.9 1.8.8-.4 1.5c-3 .3-5.9-2.6-5.6-5.6z" fill="#fff"/></svg>
      0461 738 524
    </li>
    <li class="contact__item">
      <svg class="contact__icon" viewBox="0 0 14 14" aria-hidden="true"><rect x="1" y="3" width="12" height="8" fill="#b82040"/><path d="M1.5 3.5L7 8l5.5-4.5" fill="none" stroke="#fff" stroke-width="1.2"/></svg>
      doran@kbtlaw.co
    </li>
    <li class="contact__item">
      <svg class="contact__icon" viewBox="0 0 14 14" aria-hidden="true"><circle cx="7" cy="7" r="6.5" fill="#b82040"/><path d="M.5 7h13M7 .5c-2.4 3.6-2.4 9.4 0 13M7 .5c2.4 3.6 2.4 9.4 0 13" fill="none" stroke="#fff" stroke-width="1"/></svg>
      <span>www.<span class="contact__accent">kbtlaw</span>.co</span>
    </li>
  </ul>
</section>

</body>
</html>
```